Velora Entertainment

Logo for business card design

Target Market(s)

potential film investors and screenwriters

Industry/Entity Type

Business

Contact Information for Business Card

as shown, website here is a placeholder position

Requirements
Must have
• great visual appeal
Nice to have
• harmony of colors; must evoke spirit of
• U.S.-China cooperation

```html
<!DOCTYPE html>
<html lang="en">
<head>
<meta charset="utf-8">
<title>Velora Entertainment – Business Card</title>
<link href="https://fonts.googleapis.com/css2?family=Source+Sans+3:wght@400;600;700&display=swap" rel="stylesheet">
<style>
  :root {
    --backdrop: #8f9090;
    --paper: #f3f3f4;
    --reverse-top: #a1a2a3;
    --reverse-bottom: #8a8b8c;
    --brand-red: #c8141c;
    --brand-yellow: #e3bd00;
    --brand-navy: #1b1f7d;
    --ink: #1d1d1d;
    --tab-grey: #8c8d8e;
    --on-grey: #ffffff;
  }
  * { margin: 0; padding: 0; box-sizing: border-box; }
  html, body {
    width: 1105px; height: 1200px; overflow: hidden;
    background: var(--backdrop);
    font-family: "Source Sans 3", "Myriad Pro", Arial, sans-serif;
  }
  .canvas { position: relative; width: 1105px; height: 1200px; }

  .card {
    position: absolute; left: 182px; width: 746px; height: 426px;
    box-shadow: 0 12px 22px rgba(0,0,0,0.28);
  }
  .card--front { top: 119px; background: var(--paper); }
  .card--back {
    top: 636px;
    background: linear-gradient(160deg, var(--reverse-top), var(--reverse-bottom));
  }

  .holder { position: absolute; right: 44px; top: 28px; text-align: right; }
  .holder__name { color: var(--brand-red); font-size: 26px; font-weight: 600; line-height: 1.1; }
  .holder__role { color: var(--brand-navy); font-size: 21px; font-weight: 400; line-height: 1.2; margin-top: 4px; }
  .edge-tab { position: absolute; right: 0; top: 32px; width: 17px; height: 54px; background: var(--tab-grey); }

  .wordmark { display: flex; align-items: center; gap: 14px; }
  .wordmark__mark { width: 30px; height: 30px; background: var(--brand-red); flex: none; }
  .wordmark__name { font-size: 34px; font-weight: 700; line-height: 1; letter-spacing: 0.5px; }
  .card--front .wordmark { position: absolute; left: 46px; top: 186px; }
  .card--front .wordmark__name { color: var(--brand-navy); }
  .card--back .wordmark { position: absolute; left: 0; right: 0; top: 195px; justify-content: center; }
  .card--back .wordmark__name { color: var(--on-grey); font-size: 38px; }

  .contact { position: absolute; left: 46px; top: 310px; list-style: none; }
  .contact li {
    display: flex; align-items: center; gap: 10px;
    font-size: 19px; color: var(--ink); height: 29px;
  }
  .contact svg { width: 18px; height: 18px; flex: none; }

  .address {
    position: absolute; right: 44px; top: 310px; text-align: right;
    font-size: 19px; color: var(--ink); font-style: normal; line-height: 29px;
  }
</style>
</head>
<body>
<main class="canvas">
  <section class="card card--front" aria-label="Card front">
    <div class="edge-tab"></div>
    <header class="holder">
      <p class="holder__name">Marcus Hale</p>
      <p class="holder__role">CEO/Founder</p>
    </header>

    <div class="wordmark">
      <span class="wordmark__mark"></span>
      <span class="wordmark__name">Velora Entertainment</span>
    </div>

    <ul class="contact">
      <li>
        <svg viewBox="0 0 24 24" aria-hidden="true"><path fill="#c8141c" d="M6.6 10.8a15.1 15.1 0 0 0 6.6 6.6l2.2-2.2c.3-.3.7-.4 1-.2 1.1.4 2.3.6 3.6.6.6 0 1 .4 1 1V20c0 .6-.4 1-1 1A17 17 0 0 1 3 4c0-.6.4-1 1-1h3.5c.6 0 1 .4 1 1 0 1.3.2 2.5.6 3.6.1.3 0 .7-.2 1z"/></svg>
        <span>555 214 3071</span>
      </li>
      <li>
        <svg viewBox="0 0 24 24" aria-hidden="true"><rect x="6" y="2" width="12" height="20" rx="2" fill="none" stroke="#c8141c" stroke-width="2.4"/><circle cx="12" cy="18" r="1.2" fill="#c8141c"/></svg>
        <span>555 382 9146</span>
      </li>
      <li>
        <svg viewBox="0 0 24 24" aria-hidden="true"><rect x="2" y="6" width="20" height="13" fill="#c8141c"/><path d="M2 6l10 7 10-7" fill="none" stroke="#f3f3f4" stroke-width="1.6"/></svg>
        <span>hello@velora-ent.com</span>
      </li>
    </ul>

    <address class="address">
      1420 Aurora Court<br>
      Anchorage, Alaska 99501<br>
      www.velora-ent.com
    </address>
  </section>

  <section class="card card--back" aria-label="Card back">
    <div class="wordmark">
      <span class="wordmark__mark"></span>
      <span class="wordmark__name">Velora Entertainment</span>
    </div>
  </section>
</main>
</body>
</html>
```